Professional Services - letterhead / business cards

The company (velmora partners) will provide services to Investment Funds and large investors in Spain. I have recently chosen a logo that I am attaching.

I would like a simple stationary design that i could use as letter head, business cards and "with compliments" cards.

I am not quite sure which color I will mostly use for the logo, in the email signature I will probably lean towards the white background and grey letters. I am attaching my favourite options.

Target Market(s)

Large Multinationals, Investment funds and Law firms

Industry/Entity Type

Business

Requirements
Must have
• my details are:
Luis R. Abadal
Velmora Partners S.L.
Casa de Torrelumbre
Calle de Vientoalto 27
28014 Madrid
T: +34 (91) 387-2265
M: +34 (646) 819-054
e-mail: labadal@velmorapartners.com

```html
<!DOCTYPE html>
<html lang="en">
<head>
<meta charset="utf-8">
<title>Velmora Partners – Business Cards</title>
<link rel="stylesheet" href="https://fonts.googleapis.com/css2?family=Questrial&display=swap">
<style>
  :root {
    --navy: #2b2a6e;
    --grey-text: #8a8a94;
    --card: #ffffff;
    --backdrop: #e9e8ec;
    --shadow: rgba(20, 20, 40, 0.18);
  }
  * { margin: 0; padding: 0; box-sizing: border-box; }
  html, body {
    width: 1200px; height: 719px; overflow: hidden;
    background: var(--backdrop);
    font-family: "Questrial", "Century Gothic", sans-serif;
  }
  .stage {
    position: relative; width: 1200px; height: 719px;
    display: flex; align-items: center; justify-content: center; gap: 50px;
  }
  .card {
    position: relative; width: 540px; height: 310px;
    background: var(--card); border-radius: 30px; overflow: hidden;
    box-shadow: 0 10px 28px var(--shadow);
  }
  .wordmark {
    position: absolute; color: var(--navy);
    font-size: 44px; letter-spacing: 0.5px; white-space: nowrap;
  }
  .card-front .wordmark { left: 42px; top: 48px; }
  .card-back .wordmark { left: 0; right: 0; top: 100px; text-align: center; }

  .address {
    position: absolute; left: 44px; top: 150px;
    color: var(--grey-text); font-size: 13px; line-height: 1.5;
  }
  .holder {
    position: absolute; right: 44px; top: 150px; text-align: right;
  }
  .holder-name { color: var(--navy); font-size: 19px; letter-spacing: 0.5px; }
  .holder-company { color: var(--grey-text); font-size: 12px; margin-top: 2px; }

  .contacts {
    position: absolute; left: 44px; top: 198px; list-style: none;
    color: var(--grey-text); font-size: 13px; line-height: 1.55;
  }
  .contacts li { display: flex; align-items: center; gap: 9px; }
  .contacts li:nth-child(-n+2) { color: var(--navy); }
  .contacts svg { width: 12px; height: 12px; flex: none; }

  .web-band {
    position: absolute; left: 0; right: 0; bottom: 0; height: 44px;
    background: var(--navy); color: #fff;
    font-size: 13px; letter-spacing: 5px;
    display: flex; align-items: center; padding-left: 44px;
  }
  .card-back .web {
    position: absolute; left: 0; right: 0; top: 214px; text-align: center;
    color: var(--navy); font-size: 14px; letter-spacing: 7px; font-weight: bold;
  }
</style>
</head>
<body>
<main class="stage">
  <article class="card card-front">
    <div class="wordmark">velmora partners</div>

    <address class="address" style="font-style:normal">
      Casa de Torrelumbre<br>
      Calle de Vientoalto 27, 28014 Madrid
    </address>

    <div class="holder">
      <div class="holder-name">Luis R. Abadal</div>
      <div class="holder-company">Velmora Partners S.L.</div>
    </div>

    <ul class="contacts">
      <li>
        <svg viewBox="0 0 12 12" aria-hidden="true"><circle cx="6" cy="6" r="5.3" fill="none" stroke="#2b2a6e" stroke-width="1.2"/><path d="M4 3.4c.5-.4.9-.2 1.1.3l.3.8c.1.3 0 .5-.3.7-.2.2 0 .8.4 1.3.4.5.9.8 1.1.6.3-.2.5-.2.7 0l.6.6c.3.4.2.7-.2 1-1.1.8-2.8-.4-3.7-1.7C3.3 6 3 4.3 4 3.4z" fill="#2b2a6e"/></svg>
        +34 (91) 387-2265
      </li>
      <li>
        <svg viewBox="0 0 12 12" aria-hidden="true"><rect x="3" y="0.8" width="6" height="10.4" rx="1.2" fill="none" stroke="#2b2a6e" stroke-width="1.2"/><rect x="4.3" y="2.3" width="3.4" height="4.5" fill="#2b2a6e"/><circle cx="6" cy="9.2" r="0.7" fill="#2b2a6e"/></svg>
        +34 (646) 819-054
      </li>
      <li>
        <svg viewBox="0 0 12 12" aria-hidden="true"><rect x="0.8" y="2.5" width="10.4" height="7.5" rx="1" fill="none" stroke="#2b2a6e" stroke-width="1.2"/><path d="M1 3l5 4 5-4" fill="none" stroke="#2b2a6e" stroke-width="1.2"/></svg>
        labadal@velmorapartners.com
      </li>
    </ul>

    <div class="web-band">www.velmora.com</div>
  </article>

  <article class="card card-back">
    <div class="wordmark">velmora partners</div>
    <div class="web">www.velmora.com</div>
  </article>
</main>
</body>
</html>
```